Business card design needed

Family General Practitioner/ Family Physician.
Logo is the logo of the Noble Guild of Family Healers Oceania
http://kpltw.varendo.example/ImageShelf/marks/pages/NGFHO%20mark_jpg.htm
Updates

Project Deadline Extended
Reason: Just a bit more time to make changes and the weekend for me to look at things closely and to choose. Thanks, Orin

Thanks for all the submissions. So many of them are really works of art. Not one of them are not good. The ones that I am eliminating are the ones that I think are not suitable for me personally only, and because if I don't, it makes it very difficult to decide as many of you are also sending me slight variations of a card. I have just decided to choose a second place card too. Can't thank you all enough. Good luck, Orin. P.S - Working today till 10 pm as the card says :-), so probably won't be able to give a feedback till late Saturday night or Sunday morning here in Sydney, Australia. 

Project Deadline Extended
Reason: Just added a second place to the budget and realised that Australia is ahead of the rest of the world in the time zone (only :-) - don't want to offend anyone or start a debate!! ) , so Monday deadline will mean it will be a weekend for the rest of the world. Just wanted to give everyone more time to submit their best, especially since I will be picking a second card too. Can't thank everyone enough for the submissions. P.S - Not keen on photos on the card.

Industry/Entity Type

Business

Contact Information for Business Card

Dr. Orin Halvey M.B.B.S., F.N.G.F.H.O
Family General Practitioner
Address, timings, phone and fax number on the back.

Requirements
Must have
• Timings
Mon 7 am - 7 pm
Tues 7 am - 12 pm
Wed 7 am - 10 pm
Thurs 7 am - 12 pm
Fri 7 am - 8 pm
Sat 8 am - 10 pm
Sun - Off

```html
<!DOCTYPE html>
<html lang="en">
<head>
<meta charset="utf-8">
<title>Dr. Orin Halvey – Business Card</title>
<link rel="stylesheet" href="https://fonts.googleapis.com/css2?family=Pinyon+Script&family=EB+Garamond:wght@400&family=Crimson+Pro:ital,wght@1,400&display=swap">
<style>
  :root {
    --page: #ffffff;
    --card-centre: #0b7fc6;
    --card-mid: #0a5fae;
    --card-edge: #283584;
    --ink: #ffffff;
    --ink-soft: rgba(255, 255, 255, 0.85);
  }
  html, body {
    margin: 0;
    width: 1200px;
    height: 741px;
    overflow: hidden;
    background: var(--page);
  }
  .card {
    position: absolute;
    left: 29px;
    top: 51px;
    width: 1144px;
    height: 652px;
    background: radial-gradient(ellipse 70% 75% at 48% 45%, var(--card-centre) 0%, var(--card-mid) 55%, var(--card-edge) 100%);
    color: var(--ink);
  }
  .doctor-name {
    position: absolute;
    left: 64px;
    top: 240px;
    margin: 0;
    font-family: "Pinyon Script", cursive;
    font-weight: 400;
    font-size: 66px;
    line-height: 1;
    white-space: nowrap;
  }
  .credentials {
    position: absolute;
    left: 67px;
    top: 390px;
    margin: 0;
    font-family: "EB Garamond", serif;
    font-size: 31px;
    letter-spacing: 0.5px;
    line-height: 1;
  }
  .role {
    position: absolute;
    left: 67px;
    top: 438px;
    margin: 0;
    font-family: "EB Garamond", serif;
    font-size: 38px;
    line-height: 1;
  }
  .guild-mark {
    position: absolute;
    left: 822px;
    top: 14px;
    width: 310px;
    height: 260px;
    display: flex;
    flex-direction: column;
    align-items: center;
    justify-content: center;
    gap: 18px;
  }
  .guild-mark svg {
    display: block;
  }
  .guild-name {
    margin: 0;
    font-family: "EB Garamond", serif;
    font-size: 26px;
    line-height: 1.2;
    text-align: center;
    color: var(--ink);
  }
  .tagline {
    position: absolute;
    left: 818px;
    top: 296px;
    margin: 0;
    font-family: "Crimson Pro", serif;
    font-style: italic;
    font-size: 33px;
    line-height: 1;
    color: var(--ink-soft);
    white-space: nowrap;
  }
</style>
</head>
<body>
  <main class="card">
    <div class="guild-mark">
      <svg width="90" height="90" viewBox="0 0 90 90" aria-hidden="true">
        <circle cx="45" cy="45" r="42" fill="none" stroke="#ffffff" stroke-width="3"/>
      </svg>
      <p class="guild-name">Noble Guild of<br>Family Healers Oceania</p>
    </div>
    <p class="tagline">Caring for your health</p>

    <h1 class="doctor-name">Dr. Orin Halvey</h1>
    <p class="credentials">M.B.B.S., F.N.G.F.H.O</p>
    <p class="role">Family General Practitioner</p>
  </main>
</body>
</html>
```